Natural Light/Organic/Documentary Photography Business

I like a simple, approachable, feminine, earthy/organic feel. Earth/neutral tones, nothing too loud or obnoxious. I like the watercolor look. I don't want anything too trendy or something I'll get tired of after a couple months. As far as colors, I am much more a fan of cream/taupe/blue/green...not a fan of pink or purple at all.

Target Market(s)

Weddings & Families

Industry/Entity Type

Wedding Photography

Contact Information for Business Card

website, email, phone number

Font styles to use
Other font styles liked:
• Horizontes, Gotham

Colors

Designer to choose colors to be used in the design.

Requirements
Must have
• Website: www.mirelhatchway.com
• Phone: 418.629.5073
• Email: mirel@mirelhatchway.com
Nice to have
• I like the watercolor look but its not necessary. I like simple/earthy tones. Nothing too loud or distracting. Simple & feminine without being too girly. I like an approachable/soft feel.
• Instagram: www.instagram.com/mirelhatchwayphotography/
Should not have
• NO loud colors or design or pattern. I do not want a photo of a camera or lens or anything cheesy like that.

```html
<!DOCTYPE html>
<html lang="en">
<head>
<meta charset="utf-8">
<title>Mirel Hatchway Photography – Business Card</title>
<link rel="stylesheet" href="https://fonts.googleapis.com/css2?family=Spectral+SC:wght@400&display=swap">
<style>
  :root {
    --paper: #fbfbfd;
    --mint-light: #d4f6ea;
    --mint: #aef0d6;
    --green: #86e6ad;
    --green-deep: #4fd486;
    --ink: #2c3839;
    --logo-grey: #667878;
  }
  * { margin: 0; padding: 0; box-sizing: border-box; }
  html, body {
    width: 1200px;
    height: 678px;
    overflow: hidden;
    background: var(--paper);
  }
  .card {
    position: relative;
    width: 1200px;
    height: 678px;
    background: var(--paper);
    overflow: hidden;
  }
  .watercolor-wash {
    position: absolute;
    left: 0;
    top: 0;
    width: 1200px;
    height: 678px;
  }
  .brand {
    position: absolute;
    left: 0;
    width: 1200px;
    top: 150px;
    text-align: center;
    font-family: "Spectral SC", Georgia, serif;
    font-weight: 400;
    color: var(--logo-grey);
  }
  .brand-name {
    display: block;
    font-size: 64px;
    line-height: 1;
    letter-spacing: 2px;
  }
  .brand-tagline {
    display: block;
    margin-top: 22px;
    font-size: 19px;
    letter-spacing: 14px;
    padding-left: 14px;
  }
  .contact-list {
    position: absolute;
    left: 0;
    width: 1200px;
    top: 356px;
    list-style: none;
    text-align: center;
    font-family: "Spectral SC", Georgia, serif;
    font-weight: 400;
    font-size: 17px;
    color: var(--ink);
  }
  .contact-item {
    height: 50.5px;
    line-height: 26px;
  }
  .contact-label { letter-spacing: 0.3px; }
</style>
</head>
<body>
<main class="card">
  <svg class="watercolor-wash" viewBox="0 0 1200 678" role="img" aria-label="Soft mint and green watercolor wash behind the card text">
    <defs>
      <linearGradient id="wash-fill" x1="0" y1="0" x2="0.6" y2="1">
        <stop offset="0" stop-color="var(--mint-light)" stop-opacity="0.6"/>
        <stop offset="0.35" stop-color="var(--mint)"/>
        <stop offset="0.75" stop-color="var(--green)"/>
        <stop offset="1" stop-color="var(--green-deep)"/>
      </linearGradient>
      <filter id="wash-soften" x="-10%" y="-10%" width="120%" height="120%">
        <feGaussianBlur stdDeviation="14"/>
      </filter>
    </defs>
    <path filter="url(#wash-soften)" fill="url(#wash-fill)"
      d="M160 170 C300 100 520 95 700 110 C860 120 980 150 1040 230
         C1070 300 1040 380 1050 470 C1060 560 1060 640 1050 678
         L140 678 C120 600 110 520 130 440 C150 360 100 290 160 170 Z"/>
  </svg>

  <header class="brand">
    <span class="brand-name">Mirel Hatchway</span>
    <span class="brand-tagline">PHOTOGRAPHY</span>
  </header>

  <ul class="contact-list">
    <li class="contact-item"><span class="contact-label">Cell:</span> 418.629.5073</li>
    <li class="contact-item"><span class="contact-label">Email:</span> mirel@mirelhatchway.com</li>
    <li class="contact-item"><span class="contact-label">Web:</span> www.mirelhatchway.com</li>
    <li class="contact-item"><span class="contact-label">Insta:</span> @mirelhatchwayphotography</li>
  </ul>
</main>
</body>
</html>
```